Home Page Website Design

The Site width is 1000 px. I've attached a Balsamiq mockup as a design layout guide. The design needs to be flat and clean. Please stick to the pixel dimensions of the mock up as the site will be responsive. I've also attached the logos used on the mockup for positional purposes.

Colours to use: Black, Grey, Green (Logo tie in) & green complementary colours.

Green (Logo tie in)
White Background
Titles: Black (Roboto Bold 700)
Text: Dark Grey (Roboto Normal 400)

Look & Style Example
http://www.brindlowe.org.uk/

Type Face
Google Fonts - Roboto

These are just guidelines, please feel free to use you own creative judgment.

Thanks

```html
<!DOCTYPE html>
<html lang="en">
<head>
<meta charset="utf-8">
<title>Meadowbrook Teaching Schools Alliance</title>
<link href="https://fonts.googleapis.com/css2?family=Roboto:wght@400;500;700&display=swap" rel="stylesheet">
<style>
:root{
  --green:#0aa64a;
  --green-dark:#078a3c;
  --ink:#111;
  --text:#555;
  --muted:#777;
  --panel:#f4f4f4;
  --line:#e2e2e2;
  --page:#ececec;
  --white:#fff;
}
*{box-sizing:border-box;margin:0;padding:0}
html,body{width:688px;height:1200px;overflow:hidden}
body{font-family:'Roboto',sans-serif;color:var(--text);background:var(--page);position:relative}
.abs{position:absolute}
.sheet{left:14px;top:0;width:660px;height:926px;background:var(--white)}
.brand{left:21px;top:30px;width:110px}
.brand-mark{font-size:30px;font-weight:400;color:var(--green);letter-spacing:1px;line-height:36px}
.brand-name{font-size:7px;color:var(--green);line-height:10px}
.btn{background:var(--green);color:var(--white);font-weight:700;display:flex;align-items:center;justify-content:center;border-radius:2px}
.chat{left:504px;top:13px;width:68px;height:23px;font-size:12px;gap:5px}
.chat i{width:13px;height:9px;border-radius:50%;background:#3b3b3b;display:block}
.login{left:590px;top:13px;width:76px;height:23px;font-size:12px}
.register{left:392px;top:47px;width:274px;height:49px;background:var(--panel)}
.register-label{left:13px;top:9px;font-size:8px;font-weight:500;color:#222}
.register-input{left:12px;top:23px;width:194px;height:19px;background:var(--white);font-size:7px;color:#bbb;padding:5px}
.register-submit{left:209px;top:23px;width:62px;height:19px;font-size:8px}
.nav{left:21px;top:106px;width:646px;height:32px;background:var(--green);display:flex;align-items:center;padding-left:22px;gap:19px}
.nav span{color:var(--white);font-size:11px;font-weight:500}
.hero{left:21px;top:138px;width:646px;height:289px;background:linear-gradient(90deg,#cfcac4 0%,#e9e6e2 45%,#f1efec 65%,#d8dde4 100%)}
.hero-photo{right:0;top:0;width:260px;height:289px;background:linear-gradient(180deg,#c8d2de,#a9b6c6 60%,#d9d2c6)}
.hero-card{left:31px;top:37px;width:362px;height:222px;background:rgba(243,243,243,.9);padding:17px 11px 0}
.hero-card h1{font-size:14.5px;font-weight:500;color:#333;margin-bottom:8px}
.hero-card p{font-size:9.6px;line-height:16.8px;color:#777;text-align:justify;padding:0 5px}
.find{left:13px;top:183px;width:106px;height:29px;font-size:9px;font-weight:500}
.dots{left:586px;top:268px;display:flex;gap:3px}
.dots i{width:9px;height:9px;border-radius:50%;background:var(--white);display:block}
.dots i:first-child{background:var(--green)}
.panel{background:var(--panel)}
.panel h2{font-size:13px;font-weight:700;color:var(--ink);position:absolute;left:13px;top:12px}
.welcome{left:21px;top:445px;width:207px;height:469px}
.video{left:10px;top:38px;width:185px;height:125px;background:linear-gradient(135deg,#b79c74,#d8c7a8 50%,#8a6e50)}
.video-bar{left:10px;top:146px;width:185px;height:17px;background:#2b2b2b}
.video-bar .track{left:34px;top:7px;width:123px;height:3px;background:#666}
.video-bar .fill{left:34px;top:7px;width:30px;height:3px;background:#ccc}
.video-bar .pause{left:10px;top:5px;width:6px;height:7px;border-left:2px solid #eee;border-right:2px solid #eee}
.welcome p{position:absolute;left:12px;width:182px;font-size:8.4px;line-height:15.2px;text-align:justify}
.training{left:241px;top:445px;width:206px;height:213px}
.course-link{left:12px;width:181px;height:29px;font-size:9.2px;justify-content:space-between;padding:0 10px 0 17px}
.course-link svg{width:16px;height:16px}
.news{left:241px;top:672px;width:206px;height:242px}
.news-item{position:absolute;left:12px;width:182px}
.news-item h3{font-size:10.4px;font-weight:400;color:#222;line-height:16px}
.news-item .date{font-size:8px;color:var(--green);margin:3px 0 4px}
.news-item p{font-size:8.2px;line-height:15px}
.news-item .more{font-size:8px;color:var(--green)}
.latest{left:461px;top:445px;width:206px;height:469px}
.rule{left:14px;width:178px;height:1px;background:var(--line)}
.rule i{position:absolute;left:85px;width:0;height:0;border-left:4px solid transparent;border-right:4px solid transparent}
.offer{position:absolute;left:13px;width:180px}
.offer h3{font-size:10.2px;font-weight:400;color:#222;line-height:16.5px}
.offer p{font-size:7.8px;line-height:15px;text-align:justify;margin-top:4px}
.offer .places{position:absolute;left:0;font-size:8.2px;font-weight:700;color:#222}
.offer .book{position:absolute;left:124px;width:56px;height:18px;font-size:8px;font-weight:500}
.footer{left:0;top:942px;width:688px;height:258px;background:var(--white);border-top:1px solid var(--line)}
.foot-col{position:absolute;top:28px;font-size:8px;line-height:16.4px;color:#333}
.foot-col strong{color:var(--green);font-size:9.5px;font-weight:700;display:block;line-height:16px;margin-bottom:1px}
.social{top:34px;width:22px;height:22px;border-radius:50%}
.hub{left:532px;top:63px;font-size:8.5px;color:#333;line-height:10px;display:flex;gap:4px;align-items:center}
.hub i{width:14px;height:14px;border-radius:50%;background:#9bc93b;display:block}
.divider{left:0;width:688px;height:1px;background:var(--line)}
.partners-title{left:0;top:133px;width:688px;text-align:center;font-size:9.5px;font-weight:700;color:#111}
.partners{left:22px;top:154px;width:644px;height:40px;display:flex;justify-content:space-between;align-items:center}
.partners i{display:block;border-radius:3px}
.copyright{left:0;top:225px;width:688px;text-align:center;font-size:8px;color:#333}
</style>
</head>
<body>
<div class="abs sheet"></div>

<header>
  <div class="abs brand">
    <div class="brand-mark">MTA</div>
    <div class="brand-name">Meadowbrook Teaching Schools Alliance</div>
  </div>
  <div class="abs btn chat"><i></i>CHAT</div>
  <div class="abs btn login">LOGIN</div>
  <form class="abs register">
    <div class="abs register-label">Register Now</div>
    <div class="abs register-input">Enter your E-mail ID</div>
    <div class="abs btn register-submit">Submit</div>
  </form>
  <nav class="abs nav">
    <span>Home</span><span>About Us</span><span>Training &amp; Development</span><span>Benefits</span><span>Members</span><span>What's on</span><span>Contact Us</span><span>News</span><span>forum</span>
  </nav>
</header>

<section class="abs hero">
  <div class="abs hero-photo" role="img" aria-label="Photo of a teacher explaining to a workshop group"></div>
  <div class="abs hero-card">
    <h1>New Teachers in workshop</h1>
    <p>Lorem Ipsum is simply dummy text of the printing and typesetting industry. Lorem Ipsum has been the industry's standard dummy text ever since the 1500s, when an unknown printer took a galley of type and scrambled it to make a type specimen book. It has survived not only five centuries, but also the leap into electronic typesetting, remaining essentially unchanged. It was popularised in the 1960s with the release of Letraset sheets containing Lorem Ipsum passages, and more recently with desktop publishing .</p>
    <div class="abs btn find">Find Out More</div>
  </div>
  <div class="abs dots"><i></i><i></i><i></i><i></i></div>
</section>

<section class="abs panel welcome">
  <h2>Welcome</h2>
  <div class="abs video" role="img" aria-label="Video still of a teacher reading to young pupils in a classroom"></div>
  <div class="abs video-bar"><span class="abs pause"></span><span class="abs track"></span><span class="abs fill"></span></div>
  <p style="top:179px">Lorem Ipsum is simply dummy text of the printing and typesetting industry. Lorem Ipsum has been the industry's standard dummy text ever since the 1500s, when an unknown printer took a galley of type and scrambled it to make a type specimen book. It has survived not only five centuries, but also the leap into electronic typesetting, remaining essentially unchanged. It was popularised in the 1960s with the release of Letraset sheets containing Lorem Ipsum passages, and more recently with desktop</p>
  <p style="top:361px">Lorem Ipsum is simply dummy text of the printing and typesetting industry. Lorem Ipsum has been the industry's standard dummy text ever since the 1500s, when an unknown printer took a galley of type and scrambled it to make a type specimen book. It has survived.</p>
</section>

<section class="abs panel training">
  <h2>Training &amp; Development</h2>
  <div class="abs btn course-link" style="top:38px">Leadership Training<svg viewBox="0 0 16 16"><circle cx="8" cy="8" r="8" fill="#fff"/><path d="M6 4.5 11 8 6 11.5z" fill="#0aa64a"/></svg></div>
  <div class="abs btn course-link" style="top:71px">CPD<svg viewBox="0 0 16 16"><circle cx="8" cy="8" r="8" fill="#fff"/><path d="M6 4.5 11 8 6 11.5z" fill="#0aa64a"/></svg></div>
  <div class="abs btn course-link" style="top:104px">School to school Support<svg viewBox="0 0 16 16"><circle cx="8" cy="8" r="8" fill="#fff"/><path d="M6 4.5 11 8 6 11.5z" fill="#0aa64a"/></svg></div>
  <div class="abs btn course-link" style="top:137px">Research &amp; Development<svg viewBox="0 0 16 16"><circle cx="8" cy="8" r="8" fill="#fff"/><path d="M6 4.5 11 8 6 11.5z" fill="#0aa64a"/></svg></div>
  <div class="abs btn course-link" style="top:171px">ITT (School Direct )<svg viewBox="0 0 16 16"><circle cx="8" cy="8" r="8" fill="#fff"/><path d="M6 4.5 11 8 6 11.5z" fill="#0aa64a"/></svg></div>
</section>

<section class="abs panel news">
  <h2>News</h2>
  <article class="news-item" style="top:37px">
    <h3>Lorem Ipsum is simply dummy text of the printing dummy text</h3>
    <div class="date">May 2013 ,23rd</div>
    <p>Lorem Ipsum has been the industry's standard dummy text ever since ...</p>
    <div class="more">Read More</div>
  </article>
  <article class="news-item" style="top:140px">
    <h3>Lorem Ipsum is simply dummy text of the printing dummy text</h3>
    <div class="date">May 2013 ,23rd</div>
    <p>Lorem Ipsum has been the industry's standard dummy text ever since ...</p>
    <div class="more">Read More</div>
  </article>
</section>

<section class="abs panel latest">
  <h2>Latest Courses</h2>
  <div class="abs rule" style="top:42px"><i style="top:-4px;border-bottom:4px solid #ccc"></i></div>
  <article class="offer" style="top:51px">
    <h3>Want to deliver consistently'Outstanding Lessons'</h3>
    <p>Lorem ipsum dolor sit amet, consectetur adipisicing elit, sed do eiusmod tempor incididunt ut labore et dolore magna aliqua ris.</p>
    <div class="places" style="top:89px">6 Places Left</div>
    <div class="btn book" style="top:84px">Book Now</div>
  </article>
  <div class="abs rule" style="top:175px"></div>
  <article class="offer" style="top:190px">
    <h3>Want to deliver consistently'Outstanding Lessons'</h3>
    <p>Lorem ipsum dolor sit amet, consectetur adipisicing elit, sed do eiusmod tempor incididunt ut labore et dolore magna aliqua ris.</p>
    <div class="places" style="top:89px">6 Places Left</div>
    <div class="btn book" style="top:84px">Book Now</div>
  </article>
  <div class="abs rule" style="top:325px"></div>
  <article class="offer" style="top:340px">
    <h3>Want to deliver consistently'Outstanding Lessons'</h3>
    <p>Lorem ipsum dolor sit amet, consectetur adipisicing elit, sed do eiusmod tempor incididunt ut labore et dolore magna aliqua ris.</p>
    <div class="places" style="top:89px">6 Places Left</div>
    <div class="btn book" style="top:84px">Book Now</div>
  </article>
  <div class="abs rule" style="top:449px"><i style="top:1px;border-top:4px solid #ccc"></i></div>
</section>

<footer class="abs footer">
  <div class="foot-col" style="left:21px">
    <strong>Meadowbrook teaching schools alliance</strong>
    12 Orchard Lane, Hartfield<br>HF4 2QL<br>Tel: 01632 960418<br>E-mail:info@meadowbrookteaching.co.uk
  </div>
  <div class="foot-col" style="left:240px">About Us<br>Training &amp; Development<br>Benefits<br>Members<br>Calendar of events</div>
  <div class="foot-col" style="left:406px">Contact Us<br>News<br>Forum<br><br>Site Map</div>
  <span class="abs social" style="left:537px;background:#3b5998"></span>
  <span class="abs social" style="left:569px;background:#4fb6e3"></span>
  <div class="abs hub"><i></i><span>Regional<br>Teaching<br>Hub</span></div>

  <div class="abs divider" style="top:119px"></div>
  <div class="abs partners-title">Partner Schools</div>
  <div class="abs partners" role="img" aria-label="Partner school badges">
    <i style="width:72px;height:24px;background:#d9313d"></i>
    <i style="width:52px;height:30px;background:#e46b33"></i>
    <i style="width:58px;height:24px;background:#9aaed0"></i>
    <i style="width:30px;height:32px;background:#1f3f9a"></i>
    <i style="width:30px;height:32px;background:#c9a227"></i>
    <i style="width:24px;height:34px;background:#8b2b3a"></i>
    <i style="width:22px;height:32px;background:#3a5d2f"></i>
    <i style="width:18px;height:36px;background:#c43b3b"></i>
    <i style="width:68px;height:20px;background:#2f8fd0"></i>
    <i style="width:64px;height:32px;background:#a8896a"></i>
    <i style="width:30px;height:34px;background:#1f4f8a"></i>
  </div>
  <div class="abs divider" style="top:206px"></div>
  <div class="abs copyright">Copyright ©2013&nbsp; Company Name &nbsp;&nbsp;- All rights reserved</div>
</footer>
</body>
</html>
```